A wedding company selling top 5 wedding venues in an affluent historic Florida Town

We need a word press design (Layered PSD files) to hand over to a web developer.
It's for Ashcombe Bridal Company. The company has been set up to sell wedding packages to the top 5 or so wedding venues in Elm Haven. Elm Haven is an historic Florida town which is known for it's European village feel, with paved roads and sidewalk seating for cafe's and restaurants.
Needs to be clean and fresh with an elegant feel.
We have a logo already established which you will find attached to the brief along with a few wedding photo's from a couple of the venues we will be selling.
We are starting with 4 venues, which will each have about 3 different packages. I'd like a design for a home page and an inside page.
We will have a blog, recent weddings page which we will update with photo's etc.
The home page will have tabs for:
Wedding Venues, Reception Venues, About US, Contact US, Blog,

Target Market(s)

Brides and Grooms looking for a stylish elegant wedding. Based in western speaking countries, aged between 20 - 50 years old. Probably more aimed at the female who makes the decisions.

Industry/Entity Type

Wedding

Font styles to use
Sans Serif

Colors

Designer to choose colors to be used in the design.

Requirements
Must have
• On the home page I'd like a big slider, A block with a paragraph about Elm Haven in general, a twitter feed, a recent weddings link and a big button on each page which goes to a "request info" form.

```html
<!DOCTYPE html>
<html lang="en">
<head>
<meta charset="utf-8">
<title>Ashcombe Bridal Company</title>
<link rel="stylesheet" href="https://fonts.googleapis.com/css2?family=Lato:wght@100;300&family=Open+Sans:wght@400;700&display=swap">
<style>
  :root {
    --ink: #3f3f3f;
    --ink-soft: #555;
    --body-ink: #4f4c4c;
    --rule: rgba(160,150,150,0.45);
    --panel: rgba(255,255,255,0.55);
    --brand: #7a3a9a;
    --icon: #8a8a8a;
    --photo-cream: #f3efe6;
    --photo-blush: #e9c3c0;
    --photo-edge: #d9cfc9;
    --arrow-bg: rgba(255,255,255,0.7);
  }
  * { box-sizing: border-box; margin: 0; padding: 0; }
  html, body { width: 1200px; height: 750px; overflow: hidden; }
  body { position: relative; font-family: "Open Sans", sans-serif; color: var(--ink); background: var(--photo-edge); }

  .hero-photo {
    position: absolute; inset: 0;
    background:
      radial-gradient(ellipse 470px 380px at 640px 390px, var(--photo-cream) 0%, #eddcd4 45%, var(--photo-blush) 62%, rgba(127,154,106,0.55) 75%, transparent 82%),
      linear-gradient(90deg, #d8c4bb 0%, #e9e6e2 30%, #e4e0dc 70%, #cfc8c4 100%);
  }

  .sidebar {
    position: absolute; left: 0; top: 0; width: 157px; height: 750px;
    background: var(--panel);
    border-right: 1px solid rgba(255,255,255,0.6);
  }
  .brand {
    position: absolute; left: 24px; top: 72px; width: 130px;
    font-size: 15px; font-weight: 400; line-height: 1.25; color: var(--brand);
  }
  .main-nav { position: absolute; left: 21px; top: 163px; width: 115px; list-style: none; }
  .main-nav li, .extra-nav li {
    height: 31px; border-bottom: 1px solid var(--rule);
    display: flex; align-items: center; padding-left: 7px;
    font-size: 9px; text-transform: uppercase; color: var(--ink);
  }
  .search {
    position: absolute; left: 21px; top: 346px; width: 114px; height: 20px;
    border: 1px solid #a9a3a3; background: rgba(255,255,255,0.35);
    font-size: 9px; color: #777; padding: 4px 7px;
  }
  .search svg { position: absolute; right: 6px; top: 4px; }
  .extra-nav { position: absolute; left: 21px; top: 384px; width: 115px; list-style: none; }
  .extra-nav li svg { margin-left: 3px; }
  .social { position: absolute; left: 21px; top: 669px; display: flex; gap: 5px; }
  .social span { width: 18px; height: 18px; border-radius: 50%; background: var(--icon); display: block; }
  .copyright { position: absolute; left: 21px; top: 697px; width: 100px; font-size: 7px; line-height: 1.4; color: var(--ink-soft); text-transform: uppercase; }

  .slide-title {
    position: absolute; left: 441px; top: 228px;
    font-family: "Lato", sans-serif; font-weight: 100; font-size: 76px; line-height: 0.92;
    color: var(--ink); letter-spacing: 2px;
  }
  .slide-text {
    position: absolute; left: 400px; top: 401px; width: 555px;
    text-align: center; font-size: 13.5px; font-weight: 700; line-height: 25px;
    color: var(--body-ink); letter-spacing: 0.9px; white-space: nowrap;
  }
  .slider-arrow {
    position: absolute; top: 522px; width: 56px; height: 56px; border-radius: 50%;
    background: var(--arrow-bg);
    display: flex; align-items: center; justify-content: center;
  }
  .slider-arrow.prev { left: 617px; }
  .slider-arrow.next { left: 683px; }
</style>
</head>
<body>
  <div class="hero-photo" role="img" aria-label="Close-up of a bridal bouquet of white and pale pink roses held by a bride"></div>

  <aside class="sidebar">
    <div class="brand">Ashcombe Bridal Company</div>
    <ul class="main-nav">
      <li>Weding Venues</li>
      <li>Reception Venues</li>
      <li>About Us</li>
      <li>Blog</li>
      <li>Contact Us</li>
    </ul>
    <div class="search">Search...
      <svg width="11" height="11" viewBox="0 0 11 11"><circle cx="4.5" cy="4.5" r="3.5" fill="none" stroke="#888" stroke-width="1.2"/><line x1="7" y1="7" x2="10.5" y2="10.5" stroke="#888" stroke-width="1.3"/></svg>
    </div>
    <ul class="extra-nav">
      <li>Request Info<svg width="6" height="4" viewBox="0 0 6 4"><path d="M0.5 0.5 L3 3 L5.5 0.5" fill="none" stroke="#444" stroke-width="1"/></svg></li>
      <li>Recent Wedding<svg width="6" height="4" viewBox="0 0 6 4"><path d="M0.5 0.5 L3 3 L5.5 0.5" fill="none" stroke="#444" stroke-width="1"/></svg></li>
    </ul>
    <div class="social"><span></span><span></span><span></span><span></span><span></span></div>
    <p class="copyright">2014 XYZ. All rights reserved.</p>
  </aside>

  <h1 class="slide-title">ELM<br>HAVEN</h1>
  <p class="slide-text">Integer ultrices ipsum id justo ultrices sed blandit felis ultricies.<br>Duis semper tristique congue. Pellentesque id orci sed ligula<br>elementum tempor ut non nulla. Aenean lectus nulla,<br>rutrum in tincidunt non, vestibulum a arcu</p>

  <div class="slider-arrow prev"><svg width="14" height="18" viewBox="0 0 14 18"><path d="M11 1 L3 9 L11 17" fill="none" stroke="#444" stroke-width="1.4"/></svg></div>
  <div class="slider-arrow next"><svg width="14" height="18" viewBox="0 0 14 18"><path d="M3 1 L11 9 L3 17" fill="none" stroke="#444" stroke-width="1.4"/></svg></div>
</body>
</html>
```